Corbell Lending Partners - Real estate loans - need a business card with a logo

I need a logo and a business card that looks elegant - that looks as if it is a big stablish corporation - We do real estate loans, my goal is to brand myself with colors black background - gold or silver letters - some combination - Name of the company different color than the rest of the card -

```html
<!DOCTYPE html>
<html lang="en">
<head>
<meta charset="utf-8">
<title>Corbell Lending Partners – Business Card</title>
<link rel="stylesheet" href="https://fonts.googleapis.com/css2?family=Montserrat:wght@400;500;700;800&family=Arimo:wght@400&display=swap">
<style>
  :root {
    --navy: #1c2a4a;
    --gold: #c4a56b;
    --white: #ffffff;
    --ink: #1e1e1e;
    --stage: #1a1a1c;
  }
  * { margin: 0; padding: 0; box-sizing: border-box; }
  html, body { width: 1200px; height: 786px; overflow: hidden; background: var(--stage); }
  .canvas { position: relative; width: 1200px; height: 786px; }

  .card { position: absolute; width: 530px; height: 303px; overflow: hidden; }

  /* Front */
  .card-front { left: 50px; top: 110px; background: var(--white); }
  .corner-block { position: absolute; left: 0; top: 0; width: 92px; height: 62px; background: var(--navy); }
  .corner-tab { position: absolute; right: 0; top: 0; width: 18px; height: 14px; background: var(--navy); }
  .brand-front { position: absolute; left: 40px; top: 74px; display: flex; align-items: center; gap: 10px; }
  .brand-mark { width: 16px; height: 16px; background: var(--navy); }
  .brand-name {
    font-family: "Montserrat", sans-serif; font-weight: 700; font-size: 19px;
    letter-spacing: 0.5px; color: var(--navy); line-height: 1.1;
  }
  .rule { position: absolute; left: 40px; right: 28px; top: 164px; height: 1px; background: var(--gold); }
  .person { position: absolute; right: 28px; top: 112px; text-align: right; }
  .person-name {
    font-family: "Montserrat", sans-serif; font-weight: 500; font-size: 18px;
    color: var(--gold); letter-spacing: 0.5px;
  }
  .person-title { font-family: "Arimo", sans-serif; font-size: 12px; color: var(--ink); margin-top: 2px; }
  .contacts { position: absolute; left: 40px; top: 190px; list-style: none; }
  .contacts li {
    display: flex; align-items: center; gap: 8px;
    font-family: "Arimo", sans-serif; font-size: 12px; color: var(--ink); line-height: 20px;
  }
  .contacts svg { width: 10px; height: 10px; flex: none; }
  .address {
    position: absolute; right: 28px; top: 192px; text-align: right;
    font-family: "Arimo", sans-serif; font-size: 12px; color: var(--ink); line-height: 18px; font-style: normal;
  }

  /* Back */
  .card-back { left: 620px; top: 373px; background: var(--navy); }
  .brand-back { position: absolute; left: 0; right: 0; top: 104px; display: flex; justify-content: center; align-items: center; gap: 12px; }
  .brand-back .brand-mark { background: var(--gold); width: 18px; height: 18px; }
  .brand-back .brand-name { color: var(--white); font-size: 24px; }
  .web-line { position: absolute; left: 30px; right: 30px; top: 196px; display: flex; align-items: center; gap: 14px; }
  .web-line::before, .web-line::after { content: ""; flex: 1; height: 1px; background: var(--white); opacity: 0.8; }
  .web-line span { font-family: "Arimo", sans-serif; font-size: 13px; color: var(--white); }
</style>
</head>
<body>
<main class="canvas">
  <section class="card card-front" aria-label="Business card front">
    <div class="corner-block"></div>
    <div class="corner-tab"></div>
    <div class="brand-front">
      <span class="brand-mark"></span>
      <span class="brand-name">Corbell Lending Partners</span>
    </div>
    <div class="person">
      <div class="person-name">DANIEL HARROW</div>
      <div class="person-title">Founder</div>
    </div>
    <div class="rule"></div>
    <ul class="contacts">
      <li>
        <svg viewBox="0 0 10 10"><path d="M2 1 L4 1 L4.6 3 L3.4 4 Q4.5 6 6 6.6 L7 5.4 L9 6 L9 8 Q5 9.5 1 3 Z" fill="var(--gold)"/></svg>
        555 014 2286
      </li>
      <li>
        <svg viewBox="0 0 10 10"><rect x="1" y="2" width="8" height="6" fill="none" stroke="var(--gold)" stroke-width="1"/><path d="M1 2 L5 5.5 L9 2" fill="none" stroke="var(--gold)" stroke-width="1"/></svg>
        info@corbelllending.com
      </li>
      <li>
        <svg viewBox="0 0 10 10"><circle cx="5" cy="5" r="4" fill="none" stroke="var(--gold)" stroke-width="1"/><path d="M1 5 H9 M5 1 Q2.5 5 5 9 M5 1 Q7.5 5 5 9" fill="none" stroke="var(--gold)" stroke-width="0.8"/></svg>
        www.corbelllending.com
      </li>
    </ul>
    <address class="address">418 Larkspur Avenue<br>Brookvale, WA 99000</address>
  </section>

  <section class="card card-back" aria-label="Business card back">
    <div class="brand-back">
      <span class="brand-mark"></span>
      <span class="brand-name">Corbell Lending Partners</span>
    </div>
    <div class="web-line"><span>www.corbelllending.com</span></div>
  </section>
</main>
</body>
</html>
```